Cruise Booking Website

Cruise search and booking website

This project is a redesign of a cruise booking website we did a few years ago.

The current website is located here: http://voyage.pylonworks.example/en/

It's not fully functional but gives you ad idea how miserable the old design was.

All the information about cruises, cruise lines, destinations, ports and shore excursions will be similar to http://www.sailquest.example/
Actual search pages (form, results, single result, sailing and cabin selection, ship info, booking) will have EXACTLY the same info as sailquest.example

We like the style of http://harborfleetdesk.example, it's quite modern, good spacing, not overloaded with information. So you can use it as an example of what we like, not what we want as a final result for us. Please, don't copy it. The result should not be possible to resemble the harborfleetdesk.example, because our site has to be unique. This is important!
If you submit a design that clearly reminds another cruise site it will be rejected!

Also the mockup provided is just to give you the basic structure and show what information has to be present on the page. It doesn't mean the layout has to be the same as a mockup. The layout is up to the designer.

I've updated the mockup to be more generic so it doesn't confuse you:
https://files.boxvault.example/s/k7m2qp9wz4hx/Home%20page.png

When you're adding social sharing icons like plazanet/chirpline you have to use chinese ones instead:
https://files.boxvault.example/s/t3nr8vx5lc2e/chinese-social-icons.png
Originals: http://minilk.example/qR7t

We'll start with home page first and after it's approved inner pages can be designed.

I know the cost of the project doesn't look high, but the task is straight forward and doesn't require to be very original, it's better to follow existing design and layout patterns that proved to work well.
That's why I encourage you to choose a template to build the design on top of one of https://themeparlor.example/ themes if it will save the design work, will be easier and faster for you. So it will be more like a customization than a new design from scratch.

Mockups, site map and logo files:
- https://files.boxvault.example/sh/h48dm2rs73fkpw/QvnbW2Xz8e

Website tree:
- https://sheets.papernest.example/document/d/7xPqR2mLw9sTk4VbN8cHj3YzA6eUf5GdKo1iMnBv/edit?usp=sharing
Updates

So far a lot of designs are just copying http://www.harborfleetdesk.example/ - we don't like it!

We like the style of harborfleetdesk.example, it's quite modern, good spacing, not overloaded with information. So you can use it as an example of what we like, not what we want as a final result for us. Please, don't copy it. The result should not be possible to resemble the harborfleetdesk.example, because our site has to be unique. This is important!

Target Market(s)

Chinese travellers

Industry/Entity Type

Build

Requirements
Must have
• * White, blue and red
* Large spacing, not too much information cramped into a small space like sailquest.example or the current website
* More "hidden" info in popups, tabs and so on, so not to many things are visible at the same time
* Compatible with kestrel scaffold styling (for easier coding):
- http://kestrelkit.codeshelf.example/scaffold/index.html
- http://skinmarket.example/
* Feel free to propose to build the design on top of one of https://themeparlor.example/ themes if it will save the design work, will be easier and faster for you

```html
<!DOCTYPE html>
<html lang="en">
<head>
<meta charset="utf-8">
<title>Tidewell — Cruise Booking</title>
<link href="https://fonts.googleapis.com/css2?family=Roboto:wght@300;400;500;700&display=swap" rel="stylesheet">
<style>
:root{
  --red:#d9412f;
  --blue-deep:#1b66a8;
  --blue-sea:#2c6ea3;
  --blue-sky:#4aaaea;
  --blue-light:#55b3ee;
  --grey-bg:#ebebeb;
  --grey-line:#d3d3d3;
  --text:#333;
  --muted:#8a8a8a;
  --white:#fff;
}
*{box-sizing:border-box;margin:0;padding:0}
html,body{width:798px;height:1200px;overflow:hidden}
body{font-family:"Roboto",Arial,sans-serif;color:var(--text);background:var(--white);position:relative;font-size:10px}
.abs{position:absolute}
.hero{left:0;top:0;width:798px;height:342px;background:linear-gradient(180deg,#3f78a8 0%,#2d6593 40%,#1f5a8a 70%,#275f8c 100%)}
.hero-line{left:0;top:340px;width:798px;height:3px;background:var(--red)}
.brand{left:31px;top:14px;display:flex;align-items:center;gap:8px}
.brand-mark{width:34px;height:34px;border-radius:50%;background:var(--white);opacity:.9}
.brand-name{font-size:28px;font-weight:700;color:#1e3650;letter-spacing:-.5px}
.search-box{left:504px;top:15px;width:115px;height:14px;border-radius:8px;background:var(--white);border:1px solid #cfd8e0}
.search-btn{left:625px;top:14px;color:var(--white);font-size:12px}
.adv-search{left:504px;top:35px;color:#dfe9f2;font-size:9px;text-decoration:underline}
.top-links{left:688px;top:6px;width:82px}
.top-links a{display:block;color:var(--white);font-size:9.5px;line-height:11px;white-space:nowrap;text-decoration:none;padding:2px 0 3px;border-bottom:1px solid rgba(255,255,255,.6);letter-spacing:.2px}
.top-links a:last-child{border-bottom:none}
.nav{left:29px;top:59px;width:739px;height:30px;background:#e9e9e9;display:flex;align-items:center}
.nav-item{font-size:10.5px;color:#333;padding:0 9px;height:30px;display:flex;align-items:center;gap:4px;white-space:nowrap}
.nav-item.active{background:var(--red);color:var(--white);margin-left:23px;padding:0 6px}
.caret{width:6px;height:6px}
.dropdown{left:52px;top:89px;width:97px;height:60px;background:var(--white);padding:8px 0 0 10px}
.dropdown li{list-style:none;font-size:9.5px;color:#333;margin-bottom:5px;position:relative;padding-left:10px}
.dropdown li::before{content:"";position:absolute;left:0;top:4px;width:3px;height:3px;background:var(--red)}
.welcome{left:120px;top:132px;color:var(--white);font-size:28px;font-weight:300;letter-spacing:1px}
.welcome b{font-weight:700;color:#1e3650}
.hero-copy{left:118px;top:182px;width:303px;height:69px;background:#2a8ad0;color:var(--white);font-size:9.5px;line-height:16px;padding:0 8px}
.hero-photo{left:483px;top:121px;width:176px;height:174px;background:linear-gradient(160deg,#e3c7a4 0%,#b59d86 45%,#6f8ea8 100%);border:3px solid var(--white);box-shadow:0 1px 4px rgba(0,0,0,.3)}
.badge{left:466px;top:246px;width:62px;height:62px;border-radius:50%;background:var(--white);border:3px solid var(--red);display:flex;align-items:center;justify-content:center;transform:rotate(18deg);color:var(--red);font-size:11px;line-height:11px;text-align:center;font-weight:500}
.arrow{top:173px;width:26px;height:55px;background:rgba(30,70,110,.55);display:flex;align-items:center;justify-content:center}
.hotline{left:29px;top:352px;width:171px;height:36px;border:1px solid var(--blue-deep);display:flex;align-items:center;padding-left:8px;gap:6px;background:var(--white)}
.hotline span{font-size:11px;color:#333}
.hotline strong{font-size:14px;font-weight:400;color:var(--blue-deep)}
.acct{top:362px;display:flex;align-items:center;gap:5px;font-size:10px;color:#333}
.strip{left:0;top:403px;width:798px;height:140px;background:#f7f7f7}
.card{top:403px;width:171px;height:140px;background:var(--grey-bg)}
.card-img{width:171px;height:93px}
.card h3{font-size:11px;font-weight:400;margin:11px 0 0 8px;color:#333}
.more{display:inline-flex;align-items:center;gap:5px;background:var(--white);margin:4px 0 0 8px;padding:0 6px 0 0;font-size:8.5px;color:var(--red);font-weight:500}
.more i{width:11px;height:11px;background:var(--red);color:var(--white);font-style:normal;display:flex;align-items:center;justify-content:center;font-size:10px}
.finder{left:599px;top:403px;width:170px;height:140px;border:1px solid var(--grey-line);background:var(--white)}
.finder h4{background:var(--red);color:var(--white);font-size:11px;letter-spacing:1px;text-align:center;height:20px;line-height:20px;font-weight:500}
.sel{position:absolute;height:13px;border:1px solid #9aa;font-size:8px;padding-left:3px;line-height:11px;color:#333;background:var(--white)}
.sel::after{content:"⬍";position:absolute;right:3px;top:0;font-size:8px}
.finder small{position:absolute;font-size:7px;color:#333}
.go-btn{left:620px;top:523px;width:129px;height:14px;background:var(--blue-deep);color:var(--white);font-size:9.5px;font-weight:700;letter-spacing:.8px;text-align:center;line-height:14px}
.feature-ring{width:76px;height:76px;border-radius:50%;border:1px solid var(--red);display:flex;align-items:center;justify-content:center;color:var(--red)}
.feature h3{font-size:13px;font-weight:400;color:#333}
.feature p{font-size:9.5px;color:var(--muted);line-height:11.5px;width:200px;margin-top:2px}
.feature p a,.deal p a{color:var(--red);text-decoration:none}
.divider{left:29px;top:755px;width:739px;height:1px;background:var(--red)}
.deals-title{left:29px;top:760px;font-size:23px;font-weight:300;color:#555}
.deal{top:792px;height:188px;background:#e6e6e6}
.deal-head{height:36px;color:var(--white);font-size:15px;font-weight:300;display:flex;align-items:center;justify-content:center}
.deal-body{position:absolute;left:3px;right:3px;top:54px;bottom:4px;background:var(--white)}
.deal p{font-size:9px;color:#666;line-height:11.5px;text-align:left}
.plan{display:inline-block;background:var(--red);color:var(--white);font-size:8px;font-weight:700;letter-spacing:.6px;padding:3px 10px}
.partners{left:0;top:1008px;width:798px;height:54px;background:var(--red)}
.partners h2{position:absolute;left:34px;top:12px;color:var(--white);font-size:20px;font-weight:300}
.partner-shape{position:absolute;top:18px;height:18px;background:rgba(255,255,255,.85);border-radius:3px}
.footer{left:0;top:1062px;width:798px;height:138px;background:var(--blue-sky)}
.footer ul{position:absolute;list-style:none}
.footer li{font-size:8.5px;color:#10304c;height:14px;position:relative;padding-left:10px}
.footer li::before{content:"";position:absolute;left:0;top:4px;width:3px;height:3px;background:var(--white)}
.social{position:absolute;width:19px;height:19px;border-radius:4px}
.foot-line{position:absolute;left:29px;top:100px;width:739px;height:1px;background:#2a6ea0}
.copy{position:absolute;left:0;width:798px;text-align:center;font-size:8.5px;color:#10304c}
</style>
</head>
<body>

<div class="abs hero" role="img" aria-label="Open sea seen from a cruise ship deck in blue tones"></div>
<div class="abs hero-line"></div>

<div class="abs brand"><span class="brand-mark"></span><span class="brand-name">Tidewell</span></div>
<div class="abs search-box"></div>
<div class="abs search-btn">Search</div>
<div class="abs adv-search">Advance Search</div>
<nav class="abs top-links"><a>BOOKING</a><a>ONLINE BOOKING</a><a>MEMBERS CENTRE</a></nav>

<nav class="abs nav">
  <div class="nav-item active">DESTINATIONS <svg class="caret" viewBox="0 0 6 6"><path d="M1 2l2 2 2-2" stroke="#fff" fill="none"/></svg></div>
  <div class="nav-item">CRUISE LINES <svg class="caret" viewBox="0 0 6 6"><path d="M1 2l2 2 2-2" stroke="#d9412f" fill="none"/></svg></div>
  <div class="nav-item">SHORE ACTIVITIES <svg class="caret" viewBox="0 0 6 6"><path d="M1 2l2 2 2-2" stroke="#d9412f" fill="none"/></svg></div>
  <div class="nav-item">PROMOTIONS <svg class="caret" viewBox="0 0 6 6"><path d="M1 2l2 2 2-2" stroke="#d9412f" fill="none"/></svg></div>
  <div class="nav-item">CRUISE NEWS <svg class="caret" viewBox="0 0 6 6"><path d="M1 2l2 2 2-2" stroke="#d9412f" fill="none"/></svg></div>
  <div class="nav-item">BLOG <svg class="caret" viewBox="0 0 6 6"><path d="M1 2l2 2 2-2" stroke="#d9412f" fill="none"/></svg></div>
  <div class="nav-item">FAQ(Q&amp;A) <svg class="caret" viewBox="0 0 6 6"><path d="M1 2l2 2 2-2" stroke="#d9412f" fill="none"/></svg></div>
  <div class="nav-item">CONTACT US <svg class="caret" viewBox="0 0 6 6"><path d="M1 2l2 2 2-2" stroke="#d9412f" fill="none"/></svg></div>
</nav>
<ul class="abs dropdown"><li>Destination</li><li>Ports</li><li>Ports Pages</li></ul>

<div class="abs welcome">WELCOME TO <b>Tidewell</b></div>
<div class="abs hero-copy">Cruises are offered throughout the world and for each destination there are a number of cruise lines to choose from. From contemporary cruise lines to luxury cruise lines each cruise line offers different itineraries, features and options.</div>
<div class="abs hero-photo" role="img" aria-label="Couple walking on a sunny cruise ship deck"></div>
<div class="abs badge">BEST<br>VALUE</div>
<div class="abs arrow" style="left:29px"><svg width="10" height="16" viewBox="0 0 10 16"><path d="M8 2L2 8l6 6" stroke="#fff" stroke-width="2" fill="none"/></svg></div>
<div class="abs arrow" style="left:743px"><svg width="10" height="16" viewBox="0 0 10 16"><path d="M2 2l6 6-6 6" stroke="#fff" stroke-width="2" fill="none"/></svg></div>

<div class="abs hotline">
  <svg width="18" height="24" viewBox="0 0 18 24"><path d="M4 2c2-1 3 0 4 3l1 3c0 1-1 2-2 3 1 3 3 6 5 8 1-1 2-2 3-1l2 2c1 2 0 3-2 4-5 1-13-10-11-22z" fill="#d9412f"/></svg>
  <span>Hotline:</span><strong>4008 512 390</strong>
</div>
<div class="abs acct" style="left:603px"><svg width="18" height="18" viewBox="0 0 18 18"><rect x="1" y="4" width="11" height="12" fill="none" stroke="#d9412f" stroke-width="1.6"/><path d="M8 11l8-8" stroke="#d9412f" stroke-width="2"/></svg>REGISTER</div>
<div class="abs acct" style="left:691px"><svg width="16" height="18" viewBox="0 0 16 18"><rect x="3" y="1" width="11" height="15" fill="none" stroke="#d9412f" stroke-width="1.6"/><path d="M0 9h9M6 6l3 3-3 3" stroke="#d9412f" stroke-width="1.6" fill="none"/></svg>MY ACCOUNT</div>

<div class="abs strip"></div>
<div class="abs card" style="left:29px"><div class="card-img" role="img" aria-label="Cruise ship sailing on blue sea" style="background:linear-gradient(180deg,#3a86c4,#1f5f96)"></div><h3>Cruise lines</h3><span class="more"><i>+</i>Read More</span></div>
<div class="abs card" style="left:219px"><div class="card-img" role="img" aria-label="Rocky coastline with turquoise water" style="background:linear-gradient(180deg,#7fb2d8,#3c7b8c 55%,#7b6a55)"></div><h3>Shore Activites</h3><span class="more"><i>+</i>Read More</span></div>
<div class="abs card" style="left:409px"><div class="card-img" role="img" aria-label="Golden cruise ship theatre interior" style="background:linear-gradient(180deg,#c9a35c,#7a5330 60%,#4a3a3a)"></div><h3>Cruise news</h3><span class="more"><i>+</i>Read More</span></div>

<div class="abs finder">
  <h4>FIND YOUR CRUISE</h4>
  <div class="sel" style="left:21px;top:27px;width:130px">Popular Destinations</div>
  <div class="sel" style="left:21px;top:50px;width:62px">Any Length</div>
  <div class="sel" style="left:89px;top:50px;width:62px">Any Month</div>
  <div class="sel" style="left:21px;top:73px;width:130px">Any Cruise Lines</div>
  <small style="left:21px;top:94px">AGE 25+</small>
  <small style="left:89px;top:94px">AGE 0-24</small>
  <div class="sel" style="left:21px;top:104px;width:62px">2</div>
  <div class="sel" style="left:89px;top:104px;width:62px">0</div>
</div>
<div class="abs go-btn">SEARCH CRUISE</div>

<div class="abs feature" style="left:41px;top:572px">
  <div class="feature-ring" style="margin-left:67px"><span style="font-weight:700;font-size:16px">BLOG</span></div>
</div>
<div class="abs feature" style="left:41px;top:659px"><h3>Blog</h3><p>Lorem Ipsum is simply dummy text of the printing and typesetting industry. Lorem Ipsum has been the industry's standard dummy text ever since the 1500s, <a>Learn More &nbsp;&gt;</a></p></div>

<div class="abs feature" style="left:294px;top:572px">
  <div class="feature-ring" style="margin-left:67px"><span style="font-weight:700;font-size:40px">?</span></div>
</div>
<div class="abs feature" style="left:294px;top:659px"><h3>FAQ(Q&amp;A)</h3><p>Lorem Ipsum is simply dummy text of the printing and typesetting industry. Lorem Ipsum has been the industry's standard dummy text ever since the 1500s, <a>Learn More &nbsp;&gt;</a></p></div>

<div class="abs feature" style="left:546px;top:572px">
  <div class="feature-ring" style="margin-left:68px"><svg width="40" height="28" viewBox="0 0 40 28"><path d="M4 20h32l-4 6H8z" fill="#d9412f"/><rect x="12" y="10" width="16" height="8" fill="#d9412f"/><rect x="18" y="3" width="5" height="7" fill="#d9412f"/></svg></div>
</div>
<div class="abs feature" style="left:546px;top:659px"><h3>Ports</h3><p>Lorem Ipsum is simply dummy text of the printing and typesetting industry. Lorem Ipsum has been the industry's standard dummy text ever since the 1500s, <a>Learn More &nbsp;&gt;</a></p></div>

<div class="abs divider"></div>
<div class="abs deals-title">Our Deals</div>

<div class="abs deal" style="left:29px;width:181px;top:792px;height:177px">
  <div class="deal-head" style="background:var(--blue-light);margin-top:18px;height:34px">Packages</div>
  <div class="deal-body" style="top:52px;text-align:center;padding:8px 12px 0">
    <svg width="22" height="24" viewBox="0 0 22 24"><rect x="2" y="9" width="18" height="14" fill="none" stroke="#d9412f" stroke-width="1.5"/><rect x="1" y="6" width="20" height="4" fill="none" stroke="#d9412f" stroke-width="1.5"/><path d="M11 6v17M11 6C8 1 4 2 6 6M11 6c3-5 7-4 5 0" stroke="#d9412f" stroke-width="1.5" fill="none"/></svg>
    <p style="margin-top:4px">tidewell.example offers the best cruise deals and discounts on all cruise lines and cruise vacation packages worldwide. <a>Learn More &nbsp;&gt;</a></p>
    <span class="plan" style="margin-top:8px">CHOOSE PLAN</span>
  </div>
</div>

<div class="abs deal" style="left:214px;width:182px">
  <div class="deal-head" style="background:var(--blue-deep);margin-top:19px;height:46px">Recommended</div>
  <div style="text-align:center;padding:8px 16px 0">
    <svg width="22" height="26" viewBox="0 0 22 26"><path d="M3 12h4v12H3zM7 13l5-10c2 0 3 2 2 5l-1 4h6c2 0 2 2 1 3l-2 8H7z" fill="none" stroke="#d9412f" stroke-width="1.5"/></svg>
    <p style="margin-top:4px">Let us put your mind at ease by answering questions about tickets, tipping, documentation, dress codes and more. <a>Learn More &nbsp;&gt;</a></p>
    <span class="plan" style="margin-top:6px">CHOOSE PLAN</span>
  </div>
</div>

<div class="abs deal" style="left:398px;width:182px">
  <div class="deal-head" style="background:var(--blue-deep);margin-top:19px;height:46px">Last Minute Deals</div>
  <div style="text-align:center;padding:8px 14px 0">
    <svg width="22" height="28" viewBox="0 0 22 28"><circle cx="11" cy="17" r="8" fill="none" stroke="#d9412f" stroke-width="1.5"/><path d="M11 17V12M9 3h4M11 3v6" stroke="#d9412f" stroke-width="1.5"/><circle cx="11" cy="17" r="1.6" fill="#d9412f"/></svg>
    <p style="margin-top:3px">Last minute cruises offer a great opportunity to get exceptional cruise deals, discounts, upgrades and other valuable offers on &nbsp;<a>Learn More &nbsp;&gt;</a></p>
    <span class="plan" style="margin-top:6px">CHOOSE PLAN</span>
  </div>
</div>

<div class="abs deal" style="left:583px;width:182px;height:177px">
  <div class="deal-head" style="background:var(--blue-light);margin-top:18px;height:34px">Starline Cruise Deals</div>
  <div class="deal-body" style="top:52px">
    <div class="abs" role="img" aria-label="Ship deck with pool" style="left:9px;top:7px;width:38px;height:38px;background:linear-gradient(160deg,#9ec7e6,#d6b98e)"></div>
    <p class="abs" style="left:63px;top:10px;width:112px;font-size:8.5px;line-height:10px;color:#333">4-Day Sales Event Featuring Exclusive Savings plus 3rd/4th Guest FREE</p>
    <div class="abs" role="img" aria-label="Couple on deck by the sea" style="left:9px;top:50px;width:38px;height:38px;background:linear-gradient(160deg,#7fb7e2,#e8d8c4)"></div>
    <p class="abs" style="left:63px;top:55px;width:112px;font-size:8.5px;line-height:10px;color:#333">FREE complimentary specialty dinner for 2 plus $50 onboard credit</p>
    <span class="plan abs" style="left:50px;top:93px">CHOOSE PLAN</span>
  </div>
</div>

<div class="abs partners">
  <h2>Our Partners</h2>
  <svg class="abs" style="left:264px;top:20px" width="8" height="12" viewBox="0 0 8 12"><path d="M6 1L2 6l4 5" stroke="#fff" stroke-width="2" fill="none"/></svg>
  <div class="partner-shape" style="left:286px;width:72px"></div>
  <div class="partner-shape" style="left:384px;width:48px"></div>
  <div class="partner-shape" style="left:462px;width:82px"></div>
  <div class="partner-shape" style="left:575px;width:80px"></div>
  <div class="partner-shape" style="left:684px;width:62px"></div>
  <svg class="abs" style="left:763px;top:20px" width="8" height="12" viewBox="0 0 8 12"><path d="M2 1l4 5-4 5" stroke="#fff" stroke-width="2" fill="none"/></svg>
</div>

<footer class="abs footer">
  <ul style="left:98px;top:23px"><li>Visa</li><li>About us</li><li>Contact us</li><li>Payment info</li></ul>
  <ul style="left:259px;top:23px"><li>Terms of privacy</li><li>Terms of service</li><li>Terms of insurance</li><li>Cooperation network</li></ul>
  <ul style="left:446px;top:23px"><li>Registration agreement</li><li>Cruise promotion policy</li><li>Booking process explanation</li><li>Bonus points collection policy</li></ul>
  <span class="social" style="left:641px;top:16px;background:#f0a43a"></span>
  <span class="social" style="left:680px;top:16px;background:#3b7fd0"></span>
  <span class="social" style="left:641px;top:41px;background:#e14b3b"></span>
  <span class="social" style="left:680px;top:41px;background:#63c04a"></span>
  <span class="social" style="left:641px;top:66px;background:#2e9ad8"></span>
  <span class="social" style="left:680px;top:66px;background:#e8553f"></span>
  <div class="foot-line"></div>
  <div class="copy" style="top:107px">Copyright © 2011 Tidewell 版权所有</div>
  <div class="copy" style="top:121px">京ICP备00000000号</div>
</footer>

</body>
</html>
```